Brand new letterhead, business card, email signature etc.

We are a financial company in London, UK. Our website is www.marlowvane.com. We're wanting a complete remodel of the company colours, letter head, business cards, email signatures, etc. Looking to keep the same font for the company name. I have upload a colour palette that we want to work with. We're looking for company letterhead for outgoing letters/ correspondence, letterhead for internal documentation, email signatures, e-letters. etc. Ultimately we will redesign the entire website also. It is important that our clients get a strong, secure, warm, trustworthy, solid feeling and first impression.
Updates

Designs look the same

Target Market(s)

Institutional investors, (ultra) high net worth individuals

Industry/Entity Type

Finance, Invesments banking.

Font styles to use
Other font styles liked:
• Current font is "Champagne & Limousines"

Requirements
Must have
• Must use the colours provided on the PDF uploaded to the portal. The purple = main colour. The red = accent colour.
Nice to have
• Nice to use same font as now for the company name "Corvane". Font is "Champagne & Limousines". Nice to have some reference to the old logo flower, but only subtle.
Should not have
• Do not use the colour red from our website. Use the colours provided on the colour palette PDF that I uploaded in the portal.

```html
<!DOCTYPE html>
<html lang="en">
<head>
<meta charset="utf-8">
<title>Corvane Letterhead</title>
<link rel="stylesheet" href="https://fonts.googleapis.com/css2?family=Josefin+Sans:wght@300&family=Open+Sans:wght@400;700&display=swap">
<style>
  :root {
    --backdrop: #d8d5d1;
    --paper: #e8e8e8;
    --accent-red: #cf5548;
    --plum: #47323e;
    --stone: #cfcac2;
    --text-body: #7c7c7c;
    --text-dark: #47323e;
    --divider: #c9c9c0;
  }
  * { margin: 0; padding: 0; box-sizing: border-box; }
  html, body {
    width: 1200px; height: 1200px; overflow: hidden;
    background: var(--backdrop);
  }
  .letterhead {
    position: absolute; left: 151px; top: 20px;
    width: 898px; height: 1160px;
    background: var(--paper);
    overflow: hidden;
    font-family: "Open Sans", Arial, sans-serif;
    box-shadow: 0 6px 18px rgba(0,0,0,0.18);
  }
  .top-band {
    position: absolute; left: 0; top: 0; width: 100%; height: 36px;
    background: var(--accent-red);
  }
  .contact-rail {
    position: absolute; left: 793px; top: 0; width: 46px; height: 240px;
    background: var(--plum);
  }
  .contact-icon {
    position: absolute; left: 813px; width: 26px; height: 26px;
    transform: translate(-50%, -50%);
    left: 816px;
  }
  .brand {
    position: absolute; left: 114px; top: 147px;
    display: flex; align-items: center; gap: 16px;
  }
  .brand-square {
    width: 57px; height: 57px;
    border: 1px solid var(--plum);
  }
  .brand-name {
    font-family: "Josefin Sans", Arial, sans-serif;
    font-weight: 300; font-size: 35px; letter-spacing: 6px;
    color: var(--plum); text-transform: uppercase;
    padding-top: 6px;
  }
  .contact-block {
    position: absolute; right: 116px; width: 250px;
    text-align: right;
    font-family: "Josefin Sans", Arial, sans-serif;
    font-weight: 300; font-size: 12.5px; line-height: 16px;
    color: var(--text-dark);
  }
  .contact-phone { top: 98px; }
  .contact-web { top: 153px; }
  .contact-address { top: 207px; }
  .contact-divider {
    position: absolute; left: 589px; width: 204px; height: 1px;
    background: var(--divider);
  }
  .recipient {
    position: absolute; left: 114px; top: 290px;
  }
  .recipient-name {
    font-size: 19px; font-weight: 700; color: var(--text-dark);
    margin-bottom: 8px;
  }
  .recipient-details {
    font-size: 13px; line-height: 18.7px; color: var(--text-body);
  }
  .watermark-flower {
    position: absolute; left: 28px; top: 620px; width: 520px; height: 530px;
    background: radial-gradient(ellipse at 50% 45%, rgba(200,200,200,0.35), rgba(232,232,232,0) 70%);
  }
  .letter-body {
    position: absolute; left: 114px; top: 438px; width: 669px;
    font-size: 12.9px; line-height: 18.8px; color: var(--text-body);
    text-align: justify;
  }
  .letter-body p + p { margin-top: 18.8px; }
  .signature-mark {
    position: absolute; left: 647px; top: 920px; width: 150px; height: 32px;
    background: linear-gradient(90deg, rgba(71,50,62,0.12), rgba(71,50,62,0.22));
    border-radius: 4px;
  }
  .signatory {
    position: absolute; right: 88px; top: 955px; text-align: right;
  }
  .signatory-name {
    font-size: 16.5px; font-weight: 700; color: var(--text-dark);
    text-transform: uppercase; line-height: 22px;
  }
  .signatory-role {
    font-size: 13px; color: var(--text-body); line-height: 22px;
  }
  .footer-bands {
    position: absolute; left: 0; top: 1084px; width: 898px; height: 76px;
  }
</style>
</head>
<body>
  <main class="letterhead">
    <div class="top-band"></div>
    <div class="contact-rail"></div>

    <div class="brand">
      <div class="brand-square"></div>
      <div class="brand-name">Corvane</div>
    </div>

    <div class="contact-block contact-phone">+000 12345 6789<br>+000 12345 6789</div>
    <div class="contact-divider" style="top:145px"></div>
    <div class="contact-block contact-web">urwebsitename.com<br>urname@email.com</div>
    <div class="contact-divider" style="top:195px"></div>
    <div class="contact-block contact-address">1234 Street name, town/city,<br>state/country, post/zip 012345.</div>

    <svg class="contact-icon" style="top:115px" viewBox="0 0 24 24" aria-label="Phone">
      <path fill="#fff" d="M4 9c0-3 4-4 8-4s8 1 8 4l-3 1-1-2H8l-1 2zM7 11h10l2 7H5z"/>
      <circle cx="12" cy="14.5" r="2" fill="#47323e"/>
    </svg>
    <svg class="contact-icon" style="top:170px" viewBox="0 0 24 24" aria-label="Web">
      <circle cx="12" cy="12" r="8" fill="none" stroke="#fff" stroke-width="1.6"/>
      <path d="M4 12h16M12 4c-3 3-3 13 0 16M12 4c3 3 3 13 0 16" fill="none" stroke="#fff" stroke-width="1.3"/>
    </svg>
    <svg class="contact-icon" style="top:223px" viewBox="0 0 24 24" aria-label="Address">
      <path fill="#fff" d="M12 3a6 6 0 0 0-6 6c0 4.5 6 12 6 12s6-7.5 6-12a6 6 0 0 0-6-6z"/>
      <circle cx="12" cy="9" r="2.2" fill="#47323e"/>
    </svg>

    <section class="recipient">
      <h2 class="recipient-name">Name Surname</h2>
      <div class="recipient-details">
        Senior Executive<br>
        Address goes here. Street, City, Country<br>
        contact@yourmail.com<br>
        000-987-654-321
      </div>
    </section>

    <div class="watermark-flower" role="img" aria-label="Faint outline flower decoration"></div>

    <article class="letter-body">
      <p>Lorem ipsum dolor sit amet, consectetur adipisicing elit, sed do eiusmod tempor incididunt ut labore et dolore magna aliqua. Ut enim ad minim veniam, quis nostrud exercitation ullamco laboris nisi ut aliquip ex ea commodo consequat. Duis aute irure dolor in reprehenderit in voluptate velit esse cillum dolore eu fugiat nulla pariatur. Excepteur sint occaecat cupidatat non proident, sunt in culpa qui officia deserunt mollit anim id est laborum. Sed ut perspiciatis unde omnis iste natus error sit voluptatem accusantium doloremque laudantium, totam rem aperiam, eaque ipsa quae ab illo inventore veritatis et quasi architecto beatae vitae dicta sunt explicabo. Nemo enim ipsam voluptatem quia voluptas sit aspernatur aut odit aut fugit, sed quia consequuntur magni dolores eos qui ratione voluptatem sequi nesciunt. Neque porro voluptatem sequi nesciunt. Nemo enim ipsam voluptatem quia voluptas.</p>
      <p>Lorem ipsum dolor sit amet, consectetur adipisicing elit, sed do eiusmod tempor incididunt ut labore et dolore magna aliqua. Ut enim ad minim veniam, quis nostrud exercitation ullamco laboris nisi ut aliquip ex ea commodo consequat. Duis aute irure dolor in reprehenderit in voluptate velit esse cillum dolore eu fugiat nulla pariatur. Excepteur sint occaecat cupidatat non proident, sunt in culpa qui officia deserunt mollit anim id est laborum. Sed ut perspiciatis unde omnis iste natus error sit voluptatem accusantium doloremque laudantium, totam rem aperiam, eaque ipsa quae ab illo inventore veritatis et quasi architecto beatae vitae dicta sunt explicabo. Nemo enim ipsam voluptatem quia voluptas sit aspernatur aut odit aut.</p>
      <p>Lorem ipsum dolor sit amet, consectetur adipisicing elit, sed do eiusmod tempor incididunt ut labore et dolore magna aliqua. Ut enim ad minim veniam, quis nostrud exercitation ullamco laboris nisi ut aliquip ex ea commodo consequat. .</p>
    </article>

    <div class="signature-mark" role="img" aria-label="Handwritten signature"></div>
    <div class="signatory">
      <div class="signatory-name">Name Surname</div>
      <div class="signatory-role">General Manager</div>
    </div>

    <svg class="footer-bands" viewBox="0 0 898 76" preserveAspectRatio="none" aria-hidden="true">
      <polygon points="0,0 898,0 898,76 659,76 619,5.5 0,5.5" fill="var(--plum)"/>
      <polygon points="0,15 547,15 557,30 0,30" fill="var(--stone)"/>
      <polygon points="0,31 592,31 616,76 0,76" fill="var(--accent-red)"/>
    </svg>
  </main>
</body>
</html>
```